Chamber of Commerce Web Design Project

We are working with Harborlight Chamber of Commerce. They are a new chamber of commerce forming in SoCal.
Some sites to use for inspiration:
https://brevinmarchamber.org
https://quellford.org
https://www.dorwickhavenchamber.com
https://www.tpchamber.com
https://velmorintcc.org
Thank you for taking the time to consider designing a website for us. We are web developers based in Stockton, CA, USA. Most of our projects go through the same process. Understanding this process may help you win a project with us. We custom-code all of our websites in-house. We don’t have any requirements as to what tools you use for your design, but we prefer Figma files. For any design that we label as four-stars, we send it to the client for review. The client picks the final design they want us to use. Once we complete this process, we will continue to show additional clients all the four-star sites and purchase them later. Your designs will have multiple chances to sell. For better chances of success, we ask that you follow these guidelines.
IMAGES:
If you use any images or icons in the design, we ask that you have a link to the asset so we can purchase the image/icon. Most of the designs we submit do not have the customer’s images on them unless they have some great images. Be creative; show us the feeling you are trying to portray with your image choices. Use any royalty-free site you choose. We subscribe to Adobe and mainly use their images, but we can purchase images outside of Adobe.
PLEASE NOTE: we will not submit designs to clients with watermarks on the images.
FONTS:
We ask that you identify the fonts used in the design. This can be done in a message if you want. We typically use Google Fonts and Adobe Fonts.
CONTENT:
We're always open to different content and ideas. We often submit designs with stock images so the client can see our vision. We typically take pictures after the website launch to use their images with our vision. Lorem Ipsum is fine for paragraphs, but we ask that you write the headers in correct English. We want to be able to show the vision and identify the sections of the website.
INSPIRATION:
We typically add a couple of links in the brief of websites we like to help you get started in your design.
REVISIONS:
We do not often ask for revisions of the designs unless we see something in the design that may not appeal to the client. If there are slight changes that we want to make, we do that in the development process.
FEEDBACK:
We rarely give feedback on designs during the design process. We are working on many website projects and do not have the time to provide feedback. We usually respond if your request is well thought out and asks specific questions, but a note asking “feedback, please” usually goes unanswered.

```html
<!DOCTYPE html>
<html lang="en">
<head>
<meta charset="utf-8">
<title>Harborlight Chamber of Commerce</title>
<link href="https://fonts.googleapis.com/css2?family=Roboto:wght@400;500;700;900&display=swap" rel="stylesheet">
<style>
  :root{
    --blue:#1877f2;
    --blue-dark:#0f5fd0;
    --blue-sky:#3c8ff0;
    --yellow:#fdd23a;
    --yellow-deep:#f5c518;
    --ink:#1b1b1b;
    --muted:#555;
    --grey:#666;
    --star:#f5a623;
    --white:#fff;
  }
  *{margin:0;padding:0;box-sizing:border-box}
  html,body{width:1200px;height:3415px;overflow:hidden}
  body{position:relative;font-family:'Roboto',sans-serif;color:var(--ink);background:var(--white)}
  .abs{position:absolute}
  .btn{position:absolute;display:flex;align-items:center;justify-content:center;border-radius:8px;font-size:15px;font-weight:500}
  .btn-yellow{background:var(--yellow);color:var(--ink)}
  .btn-blue{background:var(--blue);color:var(--white)}
  .section-title{position:absolute;left:0;width:1200px;text-align:center;font-size:37px;font-weight:400;color:var(--blue)}
  .section-title b{font-weight:700}

  /* header */
  .site-header{position:absolute;left:0;top:0;width:1200px;height:92px;background:var(--white);border-bottom:1px solid #e2e2e2;z-index:3}
  .brand{position:absolute;left:111px;top:20px;display:flex;align-items:center;gap:8px;color:var(--blue);font-weight:700}
  .brand-dot{width:44px;height:44px;border-radius:50%;background:var(--blue)}
  .brand-name{font-size:26px;line-height:26px;text-transform:uppercase;letter-spacing:.5px}
  .brand-sub{font-size:11px;line-height:14px;text-transform:uppercase}
  .main-nav{position:absolute;top:35px;font-size:15px;color:#333}
  .main-nav span{position:absolute;white-space:nowrap}
  .main-nav .active{color:var(--blue);font-weight:500}
  .main-nav .active::after{content:"";position:absolute;left:0;top:25px;width:42px;height:3px;border-radius:2px;background:var(--yellow)}

  /* hero */
  .hero{position:absolute;left:0;top:92px;width:1200px;height:520px;overflow:hidden}
  .hero-photo{position:absolute;inset:0;background:linear-gradient(100deg,#2f86f0 0%,#3b8cf0 40%,#2a6fd0 65%,#1c4f9e 85%,#2563c0 100%)}
  .hero h1{position:absolute;left:111px;top:70px;width:480px;font-size:43px;line-height:53px;font-weight:700;color:var(--white)}
  .hero p{position:absolute;left:111px;top:252px;width:500px;font-size:17px;line-height:28px;color:var(--white)}
  .hero-wave{position:absolute;left:0;bottom:0}

  /* partners */
  .partners{position:absolute;top:700px;left:0;width:1200px;height:50px}
  .partner{position:absolute;top:0;display:flex;align-items:center;gap:10px;font-size:30px;font-weight:700;color:#555}
  .partner i{display:block;width:34px;height:34px;background:#555;border-radius:4px}

  /* mission */
  .mission-lead{position:absolute;left:140px;top:906px;width:920px;text-align:center;font-size:19.5px;line-height:33px;font-weight:500;color:#222}
  .mission-body{position:absolute;left:160px;top:1017px;width:880px;text-align:center;font-size:14.5px;line-height:24px;color:#333}

  /* about */
  .about{position:absolute;left:0;top:1232px;width:1200px;height:574px;background:linear-gradient(90deg,#f3cf52,#f6d45a 50%,#f0cb4a)}
  .about-photo-ring{position:absolute;left:99px;top:72px;width:412px;height:412px;border-radius:50%;background:var(--white)}
  .about-photo{position:absolute;left:113px;top:86px;width:384px;height:384px;border-radius:50%;background:radial-gradient(circle at 40% 40%,#8fa6bf,#4c6586 70%,#354a66)}
  .about h2{position:absolute;left:557px;top:76px;font-size:37px;font-weight:400;color:var(--blue)}
  .about .lead{position:absolute;left:557px;top:146px;width:540px;font-size:19.5px;line-height:28.5px;font-weight:500;color:#111}
  .about .body{position:absolute;left:557px;top:246px;width:540px;font-size:15.5px;line-height:24px;color:#3a3a3a}

  /* testimonials */
  .t-card{position:absolute;top:2006px;width:311px;height:320px;background:var(--white);border-radius:14px;border-top:6px solid var(--yellow);border-bottom:10px solid var(--yellow);box-shadow:0 4px 12px rgba(0,0,0,.12);text-align:center}
  .t-avatar{position:absolute;left:111px;top:-50px;width:88px;height:88px;border-radius:50%;border:5px solid var(--yellow);background:radial-gradient(circle,#9aa3ad,#6d7782)}
  .t-name{position:absolute;left:0;width:100%;top:62px;font-size:20px;font-weight:400;color:#111}
  .t-stars{position:absolute;left:0;width:100%;top:88px;font-size:16px;letter-spacing:1px;color:var(--star)}
  .t-text{position:absolute;left:28px;width:255px;top:124px;font-size:12.5px;line-height:23px;color:var(--grey)}
  .t-arrow{position:absolute;top:2127px;width:44px;height:44px;border-radius:50%;border:1.5px solid #222;background:var(--white)}
  .divider{position:absolute;left:111px;top:2413px;width:978px;height:1px;background:var(--blue)}

  /* events */
  .events-title{position:absolute;left:110px;top:2490px;font-size:37px;font-weight:400;color:var(--blue)}
  .event-photo{position:absolute}
  .event-date{position:absolute;left:108px;top:2812px;font-size:16.5px;color:#222}
  .event-heading{position:absolute;left:110px;top:2845px;font-size:21px;font-weight:400;color:#111}
  .event-text{position:absolute;left:110px;top:2887px;width:390px;font-size:14px;line-height:22px;color:#444}

  /* footer */
  .site-footer{position:absolute;left:0;top:3040px;width:1200px;height:375px}
  .footer-brand{position:absolute;left:0;width:1200px;top:186px;display:flex;justify-content:center;align-items:center;gap:10px;color:var(--white);font-weight:700}
  .footer-nav{position:absolute;top:272px;left:0;width:1200px;font-size:19px;font-weight:500;color:var(--white)}
  .footer-nav span{position:absolute;white-space:nowrap}
  .footer-rule{position:absolute;left:0;top:321px;width:1200px;height:2px;background:var(--yellow)}
  .copyright{position:absolute;left:0;top:335px;width:1200px;text-align:center;font-size:13px;color:var(--white)}
</style>
</head>
<body>

<header class="site-header">
  <div class="brand">
    <div class="brand-dot"></div>
    <div><div class="brand-name">Harborlight</div><div class="brand-sub">Chamber of Commerce</div></div>
  </div>
  <nav class="main-nav">
    <span class="active" style="left:434px">Home</span>
    <span style="left:518px">About Us</span>
    <span style="left:623px">Membership</span>
    <span style="left:751px">Events &amp; Programs</span>
    <span style="left:923px">Resources</span>
    <span style="left:1037px">More
      <svg width="12" height="10" viewBox="0 0 12 10" style="vertical-align:1px"><path d="M2 3l4 4 4-4" fill="none" stroke="#333" stroke-width="2"/></svg></span>
  </nav>
</header>

<section class="hero">
  <div class="hero-photo" role="img" aria-label="City skyline of downtown towers with a blue tint"></div>
  <h1>Driving Growth and Opportunity for Local Businesses</h1>
  <p>Lorem ipsum dolor sit amet, consectetur adipiscing elit, sed do eiusmod tempor incididunt ut labore et</p>
  <div class="btn btn-yellow" style="left:111px;top:320px;width:156px;height:38px">Join the Chamber</div>
  <svg class="hero-wave" width="1200" height="140" viewBox="0 0 1200 140">
    <path d="M0 130 C200 60 420 70 650 100 C900 135 1070 120 1200 80 L1200 140 L0 140Z" fill="#fff"/>
    <path d="M0 135 C200 50 420 55 650 90 C900 130 1070 115 1200 65 L1200 78 C1070 125 900 140 650 106 C420 75 200 70 0 140Z" fill="var(--yellow)"/>
    <path d="M0 118 C200 40 420 45 650 80 C900 118 1070 105 1200 58" fill="none" stroke="#fff" stroke-width="6" opacity=".9"/>
  </svg>
</section>

<div class="partners">
  <div class="partner" style="left:111px"><i></i>Corvale</div>
  <div class="partner" style="left:375px"><i></i>Tidemark</div>
  <div class="partner" style="left:635px;font-weight:400;letter-spacing:4px">BRIGHTFEN</div>
  <div class="partner" style="left:895px;font-weight:400">OSTRAVA CO</div>
</div>

<h2 class="section-title" style="top:830px"><b>Our</b> Mission</h2>
<p class="mission-lead">Lorem ipsum dolor sit amet, consectetur adipiscing elit, sed do eiusmod tempor incididunt ut labore et dolore magna aliqua. Quis ipsum suspendisse ultrices gravida. Risus commodo viverra maecenas accumsan lacus vel facilisis.</p>
<p class="mission-body">Sed ut perspiciatis unde omnis iste natus error sit voluptatem accusantium doloremque laudantium, totam rem aperiam, eaque ipsa quae ab illo inventore veritatis et quasi architecto beatae vitae dicta sunt explicabo. Nemo enim ipsam voluptatem quia voluptas sit aspernatur aut odit aut fugit, sed quia consequuntur magni dolores eos qui ratione voluptatem</p>
<div class="btn btn-yellow" style="left:522px;top:1107px;width:156px;height:38px">Join the Chamber</div>

<section class="about" role="img" aria-label="Warm yellow-toned office interior background">
  <div class="about-photo-ring"></div>
  <div class="about-photo" role="img" aria-label="Two business professionals shaking hands in an office"></div>
  <h2>About Us</h2>
  <p class="lead">Lorem ipsum dolor sit amet, consectetur adipiscing elit, sed do eiusmod tempor incididunt ut labore et dolore magna aliqua. Quis ipsum suspendisse ultrices</p>
  <p class="body">Sed ut perspiciatis unde omnis iste natus error sit voluptatem accusantium doloremque laudantium, totam rem aperiam, eaque ipsa quae ab illo inventore veritatis et quasi architecto beatae vitae dicta sunt explicabo. Nemo enim ipsam voluptatem quia voluptas sit aspernatur aut odit aut fugit, sed quia consequuntur magni dolores eos qui ratione voluptatem sequi nesciunt. Neque porro quisquam est, qui dolorem ipsum</p>
  <div class="btn btn-blue" style="left:558px;top:414px;width:120px;height:37px">Read More</div>
</section>

<h2 class="section-title" style="top:1880px"><b>Client</b> Testimonials</h2>

<div class="t-arrow" style="left:44px"><svg width="44" height="44"><path d="M24 15l-7 7 7 7" fill="none" stroke="#222" stroke-width="2.5"/></svg></div>
<div class="t-arrow" style="left:1121px"><svg width="44" height="44"><path d="M19 15l7 7-7 7" fill="none" stroke="#222" stroke-width="2.5"/></svg></div>

<article class="t-card" style="left:113px">
  <div class="t-avatar" role="img" aria-label="Client portrait"></div>
  <div class="t-name">Marisol Teague</div>
  <div class="t-stars">★★★★☆</div>
  <p class="t-text">Lorem ipsum dolor sit amet, consectetur adipiscing elit, sed do eiusmod tempor incididunt ut labore et dolore magna aliqua. Quis ipsum suspendisse ultrices gravida. Risus commodo viverra maecenas accumsan lacus vel facilisis.</p>
</article>
<article class="t-card" style="left:447px">
  <div class="t-avatar" role="img" aria-label="Client portrait"></div>
  <div class="t-name">Dorian Kessler</div>
  <div class="t-stars">★★★★☆</div>
  <p class="t-text">Lorem ipsum dolor sit amet, consectetur adipiscing elit, sed do eiusmod tempor incididunt ut labore et dolore magna aliqua. Quis ipsum suspendisse ultrices gravida. Risus commodo viverra maecenas accumsan lacus vel facilisis.</p>
</article>
<article class="t-card" style="left:781px">
  <div class="t-avatar" role="img" aria-label="Client portrait"></div>
  <div class="t-name">Priya Halvorsen</div>
  <div class="t-stars">★★★★☆</div>
  <p class="t-text">Lorem ipsum dolor sit amet, consectetur adipiscing elit, sed do eiusmod tempor incididunt ut labore et dolore magna aliqua. Quis ipsum suspendisse ultrices gravida. Risus commodo viverra maecenas accumsan lacus vel facilisis.</p>
</article>

<div class="divider"></div>

<h2 class="events-title">Events &amp; Programs</h2>
<div class="event-photo" style="left:110px;top:2574px;width:385px;height:216px;background:linear-gradient(135deg,#b7bcc2,#7c6f6a 60%,#4a4446)" role="img" aria-label="Group of professionals networking on a city rooftop"></div>
<p class="event-date">Feb 2nd, 2025</p>
<h3 class="event-heading">Lorem ipsum dolor sit amet, consectetur</h3>
<p class="event-text">Lorem ipsum dolor sit amet, consectetur adipiscing elit, sed do eiusmod tempor incididunt ut labore</p>
<div class="btn btn-yellow" style="left:110px;top:2950px;width:119px;height:38px">View More</div>

<div class="event-photo" style="left:538px;top:2499px;width:266px;height:235px;background:linear-gradient(135deg,#6b5a4a,#3d3530 60%,#2a2625)" role="img" aria-label="Attendees smiling at an indoor networking event"></div>
<div class="event-photo" style="left:821px;top:2499px;width:265px;height:235px;background:linear-gradient(180deg,#3a6fd8,#1b3f8f 55%,#0d1f4a)" role="img" aria-label="Large conference audience facing a lit stage"></div>
<div class="event-photo" style="left:538px;top:2749px;width:548px;height:269px;background:linear-gradient(120deg,#c9b6a4,#8aa6b8 50%,#a9c0cc)" role="img" aria-label="Cheerful group celebrating under falling confetti"></div>

<footer class="site-footer">
  <svg class="abs" style="left:0;top:0" width="1200" height="375" viewBox="0 0 1200 375">
    <path d="M0 90 C250 20 430 60 650 90 C880 120 1050 70 1200 30 L1200 375 L0 375Z" fill="var(--blue)"/>
    <path d="M0 55 C250 -5 430 40 650 75 C880 108 1050 55 1200 20 L1200 40 C1050 80 880 125 650 95 C430 65 250 25 0 80Z" fill="var(--yellow)"/>
    <path d="M0 42 C250 -15 430 30 650 62 C880 95 1050 42 1200 8" fill="none" stroke="#f2f2f2" stroke-width="5"/>
  </svg>
  <div class="footer-brand">
    <div style="width:54px;height:54px;border-radius:50%;background:var(--white);opacity:.95"></div>
    <div><div style="font-size:34px;line-height:34px;text-transform:uppercase">Harborlight</div><div style="font-size:14px;line-height:18px;text-transform:uppercase">Chamber of Commerce</div></div>
  </div>
  <nav class="footer-nav">
    <span style="left:138px">Home</span>
    <span style="left:240px">About Us</span>
    <span style="left:369px">Membership</span>
    <span style="left:527px">Events &amp; Programs</span>
    <span style="left:739px">Resources</span>
    <span style="left:879px">Blog</span>
    <span style="left:969px">Contact Us</span>
  </nav>
  <div class="footer-rule"></div>
  <p class="copyright">Copyright © 2025 Harborlight Chamber Of Commerce. All rights reserved.</p>
</footer>

</body>
</html>
```